Brisbane IT support business needs our first website

Hi All,

We are after a new website design for our IT solutions and support business.The business name is Harbourline Computing Services Group, or HCSG for short. We provide a range of solutions and services within the IT space.

I would like to utilize the two colours in our business logo I have uploaded.

I understand this is initially for the design only aspect of the site, but I would like to engage the winner to finish coding the website and finalize after also.

Target Market(s)

Other businesses owners and home users.

Industry/Entity Type

Business

Requirements
Must have
• Nice clean and functional design utilizing our business colours from the logo.

```html
<!DOCTYPE html>
<html lang="en">
<head>
<meta charset="utf-8">
<title>HCSG – IT solutions and support</title>
<link href="https://fonts.googleapis.com/css2?family=Open+Sans:wght@400;600;700&family=Roboto:wght@400;500;700&display=swap" rel="stylesheet">
<style>
:root{
  --navy:#0e4a70;
  --navy-dark:#0b3f60;
  --orange:#f47b20;
  --text:#333;
  --grey-bg:#f1f1f1;
  --line:#d6d6d6;
  --white:#fff;
}
*{box-sizing:border-box;margin:0;padding:0}
html,body{width:854px;height:1200px;overflow:hidden;background:var(--white)}
body{position:relative;font-family:"Open Sans",sans-serif;color:var(--text)}
.abs{position:absolute}

/* header */
.brand{left:108px;top:12px;display:flex;align-items:center;gap:10px}
.brand-mark{width:64px;height:64px;border-radius:50%;background:var(--navy)}
.brand-name{font-family:"Roboto",sans-serif;font-weight:700;font-size:34px;color:var(--orange);line-height:1}
.brand-sub{font-family:"Roboto",sans-serif;font-weight:700;font-size:7px;color:var(--orange);margin-top:3px;width:120px;line-height:1.15}
.search{left:643px;top:17px;width:102px;height:20px;border:1px solid #bbb;font-family:"Roboto",sans-serif;font-size:7px;padding:6px 6px;color:#333}
.search svg{position:absolute;right:5px;top:4px}
.nav{right:109px;top:56px;display:flex;gap:20px;font-family:"Roboto",sans-serif;font-size:9.5px;color:#222;letter-spacing:.2px}

/* hero */
.hero{left:0;top:85px;width:854px;height:387px;background:linear-gradient(100deg,#b9c3cc 0%,#e2e6ea 35%,#c9cfd6 60%,#8f98a2 100%)}
.hero-caption{left:546px;top:390px;font-family:"Roboto",sans-serif;font-size:18px;color:#111;letter-spacing:.3px}
.hero-arrow{top:266px}

/* service cards */
.card{top:483px;height:142px;background:var(--navy);box-shadow:0 8px 8px -6px rgba(0,0,0,.35)}
.card-photo{position:absolute;left:0;top:0;height:142px;width:147px}
.card-body{position:absolute;left:166px;top:20px;width:136px;color:var(--white)}
.card-title{font-family:"Roboto",sans-serif;font-weight:700;font-size:11px;letter-spacing:.3px;margin-bottom:8px}
.card-text{font-size:8px;line-height:13px;letter-spacing:.2px}
.card-more{position:absolute;right:0;bottom:0;background:var(--orange);color:var(--white);font-family:"Roboto",sans-serif;font-weight:500;font-size:9px;padding:6px 8px}

/* feature columns */
.feature{top:656px;width:142px;text-align:center}
.feature-icon{height:30px;display:flex;justify-content:center;align-items:center}
.feature-title{color:var(--orange);font-weight:600;font-size:11.5px;margin-top:6px}
.feature-text{font-size:8.5px;line-height:12px;margin-top:1px}
.feature-more{display:inline-block;margin-top:9px;border:1px solid var(--orange);color:var(--orange);font-size:8px;padding:3px 7px}

/* welcome */
.welcome{left:110px;top:787px;width:636px;height:165px;background:var(--grey-bg);box-shadow:0 10px 10px -8px rgba(0,0,0,.35)}
.welcome-title{position:absolute;left:15px;top:14px;color:var(--orange);font-weight:600;font-size:12px}
.welcome-text{position:absolute;left:15px;top:36px;width:448px;font-size:8px;line-height:14.5px}
.welcome-text p+p{margin-top:4px}
.welcome-btn{position:absolute;left:16px;top:130px;background:var(--orange);color:var(--white);font-size:7.5px;font-weight:700;padding:4px 5px}
.welcome-photo{position:absolute;left:472px;top:12px;width:150px;height:153px}

/* blog */
.blog-title{left:108px;top:973px;color:var(--orange);font-weight:600;font-size:12px}
.blog-nav{left:726px;top:975px}
.footer{left:0;top:1118px;width:854px;height:82px;background:var(--navy-dark)}
.blog{left:108px;top:995px;width:638px;height:141px;background:var(--white);border:1px solid var(--line);display:flex}
.post{flex:1;position:relative;padding:14px 12px}
.post+.post{border-left:1px solid var(--line)}
.post-photo{position:absolute;left:12px;top:14px;width:97px;height:71px;border:1px solid #bbb}
.post-body{position:absolute;left:119px;top:14px;width:168px}
.post-title{color:var(--orange);font-weight:600;font-size:8.3px;line-height:12px;margin-bottom:4px}
.post-text{font-size:8.2px;line-height:13.2px}
.post-link{color:var(--orange);font-weight:600;font-size:8.3px}

.follow{left:107px;top:1151px;color:var(--white);font-weight:700;font-size:7px}
.social{left:107px;top:1164px;display:flex;gap:3px}
.social span{width:11px;height:11px;background:#3b8fd0;display:block}
.foot-links{right:107px;top:1151px;color:var(--white);font-weight:700;font-size:7px;letter-spacing:.2px}
.copyright{right:107px;top:1167px;color:var(--white);font-weight:700;font-size:7px}
</style>
</head>
<body>

<header>
  <div class="abs brand">
    <div class="brand-mark"></div>
    <div>
      <div class="brand-name">HCSG</div>
      <div class="brand-sub">HARBOURLINE COMPUTING SERVICES GROUP</div>
    </div>
  </div>
  <div class="abs search">SEARCH
    <svg width="10" height="10" viewBox="0 0 10 10"><circle cx="4" cy="4" r="3" fill="none" stroke="#999" stroke-width="1"/><line x1="6.2" y1="6.2" x2="9" y2="9" stroke="#999" stroke-width="1"/></svg>
  </div>
  <nav class="abs nav">
    <span>HOME</span><span>WHO WE ARE</span><span>PRODUCTS</span><span>SERVICES</span><span>BLOG</span><span>CONTACT US</span>
  </nav>
</header>

<section>
  <div class="abs hero" role="img" aria-label="Photo of a business team working together at laptops in a bright office"></div>
  <svg class="abs hero-arrow" style="left:86px" width="20" height="32" viewBox="0 0 20 32"><polyline points="16,2 4,16 16,30" fill="none" stroke="#fff" stroke-width="4"/></svg>
  <svg class="abs hero-arrow" style="left:746px" width="20" height="32" viewBox="0 0 20 32"><polyline points="4,2 16,16 4,30" fill="none" stroke="#fff" stroke-width="4"/></svg>
  <div class="abs hero-caption">IT solutions and support</div>
</section>

<section>
  <article class="abs card" style="left:108px;width:314px">
    <div class="card-photo" role="img" aria-label="Photo of a smiling support agent wearing a headset" style="background:linear-gradient(120deg,#e8e8ea,#c8b6b2 60%,#d7d9de)"></div>
    <div class="card-body">
      <div class="card-title">SUPPORT SERVICES</div>
      <div class="card-text">Contrary to popular belief, Lorem Ipsum is not simply random text. It has roots in a piece of classical Latin.</div>
    </div>
    <div class="card-more">MORE</div>
  </article>
  <article class="abs card" style="left:430px;width:315px">
    <div class="card-photo" role="img" aria-label="Photo of a hand drawing a coloured pie chart on a screen" style="background:linear-gradient(120deg,#1c3448,#1f5f7c 55%,#2c7f9a)"></div>
    <div class="card-body">
      <div class="card-title">IT CONSULTING</div>
      <div class="card-text">Contrary to popular belief, Lorem Ipsum is not simply random text. It has roots in a piece of classical Latin.</div>
    </div>
    <div class="card-more">MORE</div>
  </article>
</section>

<section>
  <div class="abs feature" style="left:107px">
    <div class="feature-icon"><svg width="26" height="18" viewBox="0 0 26 18"><rect x="1" y="1" width="24" height="16" fill="none" stroke="#1d3f5a" stroke-width="2"/><polyline points="1,1 13,11 25,1" fill="none" stroke="#1d3f5a" stroke-width="2"/></svg></div>
    <div class="feature-title" style="margin-top:8px">Email Protection</div>
    <div class="feature-text">Lorem Ipsum is simply dummy text of the printing and typesetting industry.</div>
    <div class="feature-more">MORE</div>
  </div>
  <div class="abs feature" style="left:273px">
    <div class="feature-icon"><svg width="22" height="26" viewBox="0 0 22 26"><g fill="none" stroke="#1d3f5a" stroke-width="1.6"><ellipse cx="11" cy="4" rx="9" ry="3"/><path d="M2 4v18c0 1.7 4 3 9 3s9-1.3 9-3V4"/><path d="M2 10c0 1.7 4 3 9 3s9-1.3 9-3M2 16c0 1.7 4 3 9 3s9-1.3 9-3"/></g></svg></div>
    <div class="feature-title">Data Backup</div>
    <div class="feature-text">Lorem Ipsum is simply dummy text of the printing and typesetting industry.</div>
    <div class="feature-more">MORE</div>
  </div>
  <div class="abs feature" style="left:440px">
    <div class="feature-icon"><svg width="30" height="28" viewBox="0 0 30 28"><g fill="none" stroke="#1d3f5a" stroke-width="1.5"><path d="M10 12a5 5 0 1 1 10 0c0 3-3 4-3 7h-4c0-3-3-4-3-7z"/><line x1="12.5" y1="22" x2="17.5" y2="22"/><line x1="13" y1="25" x2="17" y2="25"/><line x1="15" y1="1" x2="15" y2="4"/><line x1="4" y1="12" x2="7" y2="12"/><line x1="23" y1="12" x2="26" y2="12"/><line x1="7" y1="4" x2="9" y2="6"/><line x1="23" y1="4" x2="21" y2="6"/></g></svg></div>
    <div class="feature-title">Solutions offerings</div>
    <div class="feature-text">Lorem Ipsum is simply dummy text of the printing and typesetting industry.</div>
    <div class="feature-more">MORE</div>
  </div>
  <div class="abs feature" style="left:604px">
    <div class="feature-icon"><svg width="28" height="24" viewBox="0 0 28 24"><g fill="#1d3f5a"><path d="M2 6l12-5 12 5-12 5z"/><path d="M3 9l10 4v10L3 19z"/><path d="M25 9l-10 4v10l10-4z"/></g></svg></div>
    <div class="feature-title">Open Source</div>
    <div class="feature-text">Lorem Ipsum is simply dummy text of the printing and typesetting industry.</div>
    <div class="feature-more">MORE</div>
  </div>
</section>

<section class="abs welcome">
  <h2 class="welcome-title">Welcome to our site</h2>
  <div class="welcome-text">
    <p>Lorem Ipsum is simply dummy text of the printing and typesetting industry. Lorem Ipsum has been the industry's standard dummy text ever since the 1500s, when an unknown printer took a galley of type and scrambled it to make a type specimen book. It has survived not only five centuries, but also the leap into electronic typesetting, remaining essentially unchanged.</p>
    <p>It has survived not only five centuries, but also the leap into electronic typesetting, remaining essentially unchanged.</p>
  </div>
  <div class="welcome-btn">READ MORE</div>
  <div class="welcome-photo" role="img" aria-label="Photo of two business people in grey suits standing with arms crossed" style="background:linear-gradient(180deg,#f1f1f1 0%,#9a9a9e 35%,#55575c 100%)"></div>
</section>

<div class="abs footer"></div>

<h2 class="abs blog-title">Blog</h2>
<svg class="abs blog-nav" width="20" height="12" viewBox="0 0 20 12"><polyline points="6,1 2,6 6,11" fill="none" stroke="#555" stroke-width="1.6"/><polyline points="14,1 18,6 14,11" fill="none" stroke="#555" stroke-width="1.6"/></svg>

<section class="abs blog">
  <article class="post">
    <div class="post-photo" role="img" aria-label="Photo of colleagues meeting in a bright office" style="background:linear-gradient(120deg,#9fb3c4,#d9dde2 50%,#8a8f96)"></div>
    <div class="post-body">
      <div class="post-title">Lorem Ipsum is simply dummy text of the printing and typesetting.</div>
      <div class="post-text">It has survived not only five centuries, but also the leap into electronic typesetting, remaining essentially unchanged.Contrary to popular belief, Lorem Ipsum is not simply random text. It has roots in a piece.</div>
      <div class="post-link">Read More</div>
    </div>
  </article>
  <article class="post">
    <div class="post-photo" role="img" aria-label="Photo of two business people shaking hands across a desk" style="background:linear-gradient(120deg,#c8d0d8,#e6e8eb 45%,#4a4f57)"></div>
    <div class="post-body">
      <div class="post-title">Lorem Ipsum is simply dummy text of the printing and typesetting.</div>
      <div class="post-text">It has survived not only five centuries, but also the leap into electronic typesetting, remaining essentially unchanged.Contrary to popular belief, Lorem Ipsum is not simply random text. It has roots in a piece.</div>
      <div class="post-link">Read More</div>
    </div>
  </article>
</section>

<footer>
  <div class="abs follow">FOLLOW US ON</div>
  <div class="abs social"><span></span><span></span><span></span></div>
  <div class="abs foot-links">HOME &nbsp;|&nbsp; WHO WE ARE &nbsp;|&nbsp; SERVICES &nbsp;|&nbsp; BLOG &nbsp;|&nbsp; CONTACT US</div>
  <div class="abs copyright">COPYRIGHTS @ 2014 ALL RIGHTS RESERVED</div>
</footer>

</body>
</html>
```